New Business Card Design for Manufacturing

We are an engineering/manufacturing company that offers Advanced machining/assembly/engineering services, as well as innovative products for the heavy duty engine cooling markets.

We are looking to get a new business card designed that is clean and modern looking, but still fits the wide range of technical/skilled work we do.

- We hope to use this design as the base for other design work in new Presentations, web, and print work.

Industry/Entity Type

Engineering

Contact Information for Business Card

Our preferred color of blue is (RGB) 22/71/159 but can vary slightly from that color. Our content will be our Logo and full company name (Vantrell Forge Works, Inc.), company address, name, job title, phone number with extension, cell number, fax number, website, and email address on the cards.
We'd like the full company name next to the logo, but we are open to other interpretations of that layout.
Preferably, we would like the back side to be clean with just our logo, and the front to contain all of the contact information.

Colors
2f74b4
0355a3
85abd2

Requirements
Must have
• - Logo, company name, needed content - We are open to interpretation beyond that.
• - Standard size business card.
• - Horizontal orientation.
• - Enough space for lengthy names / job titles (for example, a job title could read "Directory of Human Resources" or "V.P. of Governmental Affairs"). We need this to look clean, whether the title be short (CEO) or long (as described above).

```html
<!DOCTYPE html>
<html lang="en">
<head>
<meta charset="utf-8">
<title>Vantrell Forge Works – Business Card</title>
<link rel="stylesheet" href="https://fonts.googleapis.com/css2?family=Open+Sans:wght@400;600;700&display=swap">
<style>
  :root {
    --page-bg: #5a5a5c;
    --card-bg: #1d1d1f;
    --brand-blue: #1a6cc2;
    --rule-blue: #1f72c9;
    --gloss: #3b3b3e;
    --text-light: #e6e6e6;
    --text-muted: #bdbdbd;
  }
  * { box-sizing: border-box; margin: 0; padding: 0; }
  html, body {
    width: 799px; height: 1200px; overflow: hidden;
    background: var(--page-bg);
    font-family: "Open Sans", Arial, sans-serif;
  }
  .card {
    position: absolute; left: 90px;
    width: 620px; height: 354px;
    background: var(--card-bg);
    box-shadow: 0 10px 28px rgba(0,0,0,.45);
  }
  .card--back { top: 123px; }
  .card--front { top: 723px; }

  .back-wordmark {
    position: absolute; inset: 0;
    display: flex; align-items: center; justify-content: center;
    font-weight: 700; font-size: 64px; letter-spacing: 1px;
    color: var(--gloss);
  }

  .front-wordmark {
    position: absolute; left: 40px; top: 62px;
    font-weight: 700; font-size: 40px; line-height: 1;
    color: var(--brand-blue);
  }
  .contact {
    position: absolute; left: 352px; top: 52px; width: 250px;
    color: var(--text-light);
  }
  .contact__name {
    font-size: 23px; font-weight: 400; color: var(--brand-blue); line-height: 1.1;
  }
  .contact__title {
    font-size: 13px; color: var(--text-muted); margin: 2px 0 10px;
  }
  .contact__list { list-style: none; font-size: 13.5px; line-height: 20px; }
  .contact__list li { display: flex; align-items: center; gap: 8px; }
  .contact__list svg { width: 11px; height: 11px; flex: none; fill: var(--brand-blue); }
  .contact__address { font-size: 13.5px; line-height: 20px; margin-top: 2px; }

  .card-rule {
    position: absolute; left: 30px; right: 30px; top: 262px;
    height: 1px; background: var(--rule-blue);
  }
  .company-name {
    position: absolute; left: 120px; top: 280px;
    font-size: 17px; font-weight: 600; color: var(--text-light);
  }
</style>
</head>
<body>

<section class="card card--back" aria-label="Card back">
  <div class="back-wordmark">Vantrell</div>
</section>

<section class="card card--front" aria-label="Card front">
  <div class="front-wordmark">Vantrell</div>

  <div class="contact">
    <p class="contact__name">Marisol Keane</p>
    <p class="contact__title">Managing Director</p>
    <ul class="contact__list">
      <li><svg viewBox="0 0 24 24" aria-hidden="true"><path d="M6.6 10.8a15 15 0 0 0 6.6 6.6l2.2-2.2c.3-.3.7-.4 1-.2 1.1.4 2.3.6 3.6.6.6 0 1 .4 1 1V20c0 .6-.4 1-1 1A17 17 0 0 1 3 4c0-.6.4-1 1-1h3.5c.6 0 1 .4 1 1 0 1.3.2 2.5.6 3.6.1.3 0 .7-.2 1z"/></svg>216-555-0148 (VFW)</li>
      <li><svg viewBox="0 0 24 24" aria-hidden="true"><path d="M7 1h10a2 2 0 0 1 2 2v18a2 2 0 0 1-2 2H7a2 2 0 0 1-2-2V3a2 2 0 0 1 2-2zm0 3v14h10V4z"/></svg>216-555-0193</li>
      <li><svg viewBox="0 0 24 24" aria-hidden="true"><path d="M6 2h10l2 2v5h2a2 2 0 0 1 2 2v8h-4v3H6v-3H2v-8a2 2 0 0 1 2-2h2zm2 2v5h8V4zm0 12v4h8v-4z"/></svg>216-555-0127</li>
      <li><svg viewBox="0 0 24 24" aria-hidden="true"><path d="M12 2a10 10 0 1 0 0 20 10 10 0 0 0 0-20zm0 2c.9 0 2.2 1.9 2.8 5H9.2C9.8 5.9 11.1 4 12 4zM4.3 11h3.1a20 20 0 0 0 0 2H4.3a8 8 0 0 1 0-2zm5 0h5.4a18 18 0 0 1 0 2H9.3a18 18 0 0 1 0-2zm7.3 0h3.1a8 8 0 0 1 0 2h-3.1a20 20 0 0 0 0-2zM9.2 15h5.6c-.6 3.1-1.9 5-2.8 5s-2.2-1.9-2.8-5z"/></svg>www.vantrellforge.com</li>
      <li><svg viewBox="0 0 24 24" aria-hidden="true"><path d="M2 5h20v14H2zm2 2v.5l8 5 8-5V7zm0 2.8V17h16V9.8l-8 5z"/></svg>mkeane@vantrellforge.com</li>
    </ul>
    <p class="contact__address">58 Harlow Rd., Brennick,<br>Ohio, US 44810</p>
  </div>

  <div class="card-rule"></div>
  <p class="company-name">Vantrell Forge Works, Inc.</p>
</section>

</body>
</html>
```